TALMORK

The business want a professional looking business card. We have a scetch we will add but want the extra upgrade, and would like more suggestions for variations of our business cards.

```html
<!DOCTYPE html>
<html lang="en">
<head>
<meta charset="utf-8">
<title>TALMORK Business Card</title>
<link href="https://fonts.googleapis.com/css2?family=Montserrat:wght@400;500;700&family=Cinzel:wght@600&display=swap" rel="stylesheet">
<style>
  :root {
    --page-bg: #141414;
    --card-bg: #1e1e1e;
    --card-bg-deep: #191919;
    --gold: #c9a247;
    --gold-deep: #9c7a2c;
    --text-light: #f2f2f2;
    --emboss-light: #3a3a3a;
    --emboss-dark: #161616;
  }
  * { margin: 0; padding: 0; box-sizing: border-box; }
  html, body {
    width: 1200px; height: 1059px; overflow: hidden;
    background: var(--page-bg);
    font-family: "Montserrat", Arial, sans-serif;
  }
  .canvas { position: relative; width: 1200px; height: 1059px; }
  .card {
    position: absolute;
    border-radius: 16px;
    background: var(--card-bg);
    overflow: hidden;
  }
  .card--front { left: 257px; top: 89px; width: 687px; height: 390px; }
  .card--back  { left: 254px; top: 546px; width: 693px; height: 394px; }

  .wordmark {
    position: absolute;
    font-family: "Montserrat", Arial, sans-serif;
    font-weight: 500;
    color: var(--gold);
    white-space: nowrap;
  }
  .tagline {
    position: absolute;
    font-family: "Cinzel", Georgia, serif;
    font-weight: 600;
    color: var(--gold);
    white-space: nowrap;
  }
  .card--front .wordmark { left: 37px; top: 62px; font-size: 42px; letter-spacing: 15px; }
  .card--front .tagline { left: 118px; top: 118px; font-size: 14px; letter-spacing: 7px; }

  .accent-bar {
    position: absolute; left: 0; top: 176px; width: 20px; height: 42px;
    background: linear-gradient(180deg, var(--gold), var(--gold-deep));
  }
  .holder-name {
    position: absolute; left: 41px; top: 170px;
    font-size: 25px; font-weight: 700; color: var(--gold); white-space: nowrap;
  }
  .holder-role {
    position: absolute; left: 41px; top: 200px;
    font-size: 20px; font-weight: 400; color: var(--text-light);
  }
  .contact-list { position: absolute; left: 38px; top: 254px; list-style: none; }
  .contact-item {
    display: flex; align-items: center; height: 34px;
    font-size: 20px; color: var(--text-light); white-space: nowrap;
  }
  .contact-icon { width: 16px; height: 16px; margin-right: 10px; flex: none; }

  .emblem-area {
    position: absolute; left: 361px; top: 0; width: 326px; height: 390px;
    background: radial-gradient(ellipse at 62% 48%, var(--emboss-light) 0%, #262626 40%, var(--card-bg) 75%);
  }
  .pattern-area {
    position: absolute; inset: 0;
    background: linear-gradient(100deg, var(--emboss-dark) 0%, #222 45%, #3c3c3c 100%);
  }
  .back-lockup {
    position: absolute; left: 405px; top: 180px; width: 280px; text-align: center;
  }
  .brand-dot {
    display: block; width: 40px; height: 40px; border-radius: 50%;
    margin: 0 auto 18px; background: var(--gold);
  }
  .card--back .wordmark { position: static; font-size: 24px; letter-spacing: 7px; }
  .card--back .tagline { position: static; display: block; margin-top: 4px; font-size: 8px; letter-spacing: 4px; }
</style>
</head>
<body>
<main class="canvas">
  <section class="card card--front" aria-label="Card front">
    <div class="wordmark">TALMORK</div>
    <div class="tagline">SINCE 2026</div>

    <div class="accent-bar"></div>
    <div class="holder-name">Sander Holm Vik</div>
    <div class="holder-role">CEO &amp; Founder</div>

    <ul class="contact-list">
      <li class="contact-item">
        <svg class="contact-icon" viewBox="0 0 16 16" aria-hidden="true"><path fill="#c9a247" d="M3 1.5l2.4-.5 1.5 3.4-1.6 1.2a8 8 0 0 0 4.1 4.1l1.2-1.6 3.4 1.5-.5 2.4c-.2.8-.9 1.3-1.7 1.2C6.3 12.6 3.4 9.7 1.8 4.2 1.7 3.4 2.2 1.7 3 1.5z"/></svg>
        004791234567
      </li>
      <li class="contact-item">
        <svg class="contact-icon" viewBox="0 0 16 16" aria-hidden="true"><path fill="#c9a247" d="M1 6l7-4.5L15 6v8H1z"/><path fill="#1e1e1e" d="M2 7l6 4 6-4v.2L8 11.6 2 7.2z"/></svg>
        talmork.llc@mailbox.com
      </li>
      <li class="contact-item">
        <svg class="contact-icon" viewBox="0 0 16 16" aria-hidden="true"><circle cx="8" cy="8" r="7" fill="#c9a247"/><path fill="#1e1e1e" d="M5 3.5c1.5.5 2 1.8 1 2.8S4 8 5 9.5 4 12 3 11a6 6 0 0 1 2-7.5zM10 9c1-.5 2.5 0 2.5 1.5S11 13 10 12.5z"/></svg>
        www.talmork.llc
      </li>
    </ul>

    <div class="emblem-area" role="img" aria-label="Large blind-embossed floral ornament decoration"></div>
  </section>

  <section class="card card--back" aria-label="Card back">
    <div class="pattern-area" role="img" aria-label="Repeating embossed floral ornament pattern fading from black to grey"></div>
    <div class="back-lockup">
      <span class="brand-dot"></span>
      <div class="wordmark">TALMORK</div>
      <span class="tagline">SINCE 2026</span>
    </div>
  </section>
</main>
</body>
</html>
```